Website Redesign - We Need Your Magic!

Hello we are looking for you to help us re-design a high end and professional website for a high-end private school.

Here is the current site: http://www.ferndalecrest.com/

NOTE THIS IS DESIGN ONLY, NO CODING :)

The image they want to portray is that of high quality sports and education, in a creative "un-stiff" way.

Menu Bar: Horizontal

Look and Feel:

Site Colors: Dark green and a Gold yellow (logos are attached)

This site will represent a school so the look must be clean, bold, and classy. The site must have a very clean user interface, with things easily recognizable. Think simple.

The site should be visually appealing! If you come to me with templates, or a ton of text you will be out.

This site should be outside the box, we do not want boring, we do not want status quo. This site should instill excitement, innovation, and athletics.

So the main points again are:

1. High-end and classy look, with creative feel
2. Simple and clear navigation style
3. To cover the Junior and High School - Ferndale Crest College Schools

Think outside the box. We look forward to seeing what you come up with!!

Thank you for helping us create an amazing site for the school!

Industry/Entity Type

School

```html
<!DOCTYPE html>
<html lang="en">
<head>
<meta charset="utf-8">
<title>Ferndale Crest College</title>
<link href="https://fonts.googleapis.com/css2?family=Arimo:ital,wght@0,400;0,700;1,400&family=Open+Sans:wght@600;700&display=swap" rel="stylesheet">
<style>
:root{
  --green-dark:#0c3f1b;
  --green:#11501f;
  --gold:#cfc81e;
  --gold-btn:#e2b50e;
  --page:#f4f4f4;
  --text:#2b2b2b;
  --footer:#262626;
  --footer-bar:#1a1a1a;
  --rule:#d6d6d6;
}
*{box-sizing:border-box;margin:0;padding:0}
html,body{width:847px;height:1200px;overflow:hidden}
body{position:relative;background:var(--page);font-family:"Arimo",Arial,sans-serif;color:var(--text)}
.abs{position:absolute}

/* header */
.brand-mark{left:80px;top:20px;width:104px;height:96px;display:flex;flex-direction:column;align-items:center;justify-content:center;gap:6px}
.brand-mark .dot{width:54px;height:54px;border-radius:50%;background:var(--green)}
.brand-mark span{font-size:9px;font-weight:700;color:var(--green);letter-spacing:.5px}
.site-title{left:198px;top:44px;font-size:26px;font-weight:700;color:var(--green);letter-spacing:.3px}
.tagline{left:199px;top:91px;font-size:12.5px;font-style:italic;color:#222}
.contact{left:608px;font-size:11.5px;color:#111;display:flex;align-items:center;gap:10px}
.contact.phone{top:49px;font-weight:700}
.contact.mail{top:68px;text-decoration:underline}
.search{left:606px;top:100px;width:153px;height:25px;display:flex}
.search input{flex:1 1 auto;width:0;min-width:0;border:1px solid #ddd;background:#fff;font:9.5px "Arimo",sans-serif;color:#888;padding-left:7px}
.search button{flex:0 0 35px;width:35px;background:#111;color:#fff;border:0;font:600 12px "Open Sans",sans-serif;border-radius:0 3px 3px 0}

/* nav */
.nav{left:0;top:138px;width:847px;height:35px;background:var(--green-dark)}
.nav a{position:absolute;top:0;height:35px;line-height:35px;color:#fff;font-size:10px;text-decoration:none;text-align:center;border-right:1px solid #1f5a2d}
.nav a.current{text-align:left}
.nav a.current span{display:inline-block;background:var(--gold);color:#111;width:69px;height:23px;line-height:23px;text-align:center;vertical-align:middle;margin-top:-2px}
.nav a:last-child{border-right:0}

/* hero */
.hero{left:0;top:173px;width:847px;height:278px;background:linear-gradient(120deg,#6b5a48 0%,#9fb6a4 35%,#d9d6cf 60%,#8f8a90 100%)}
.hero-caption{left:522px;top:192px;width:254px;height:61px;background:rgba(10,10,10,.88);text-align:center;font-family:"Open Sans",sans-serif}
.hero-caption .main{color:#fff;font-size:23px;font-weight:600;margin-top:3px;line-height:28px}
.hero-caption .sub{color:var(--gold);font-size:16px;font-weight:600;line-height:22px}

/* main */
.main-col{left:80px;top:465px;width:456px}
h1{font-size:19px;font-weight:700;color:#333;margin-bottom:12px}
h2{font-size:15.5px;font-weight:700;color:#333;letter-spacing:.3px}
.main-col p{font-size:9.6px;line-height:14px;margin-bottom:14px}
.main-col p strong.accent{color:var(--green)}
.head-msg{display:flex;gap:13px;margin:11px 0 22px}
.head-photo{width:102px;height:88px;flex:none;border:3px solid #ccc;background:linear-gradient(160deg,#1d5a3a,#c9a58b 60%,#b7ac8a)}

/* sidebar */
.signup{left:557px;top:473px;width:210px;height:183px;background:var(--green-dark);border-radius:3px;padding:10px 10px}
.signup h3{color:#fff;font-size:18px;font-weight:700;letter-spacing:.5px}
.signup p{color:#dfe6df;font-size:9px;line-height:13px;margin:6px 0 8px}
.signup input{display:block;width:177px;height:24px;border:0;background:#fff;font:8.5px "Arimo",sans-serif;color:#888;padding-left:6px;margin-bottom:13px}
.signup button{width:103px;height:25px;border:0;border-radius:3px;background:linear-gradient(#f3cb2a,var(--gold-btn));font:700 12px "Arimo",sans-serif;color:#111;letter-spacing:.5px;margin-top:-4px}
.side-block{left:555px;width:212px}
.side-block h2{margin-bottom:8px}
.side-rule{height:3px;background:linear-gradient(90deg,var(--gold) 0 32px,var(--green) 32px)}
.side-list{list-style:none;margin-top:6px;width:203px}
.side-list li{position:relative;padding-left:16px;border-bottom:1px dotted var(--rule);font-size:9.6px;color:#222}
.side-list li::before{content:"";position:absolute;left:4px;top:50%;margin-top:-3.5px;border-left:4px solid #222;border-top:3.5px solid transparent;border-bottom:3.5px solid transparent}
.events li{height:25.5px;line-height:25.5px}
.links li{height:25.5px;line-height:25.5px;font-size:8px}
.side-list li:last-child{border-bottom:0}

/* footer */
.footer{left:0;top:1050px;width:847px;height:123px;background:var(--footer)}
.foot-sep{top:1065px;width:0;height:98px;border-left:1px dotted #555}
.foot-pin{left:78px;top:1088px}
.foot-name{left:128px;top:1088px;color:#fff;font-size:13px;font-weight:700;letter-spacing:.3px}
.foot-addr{left:128px;top:1106px;width:123px;text-align:right;color:#ddd;font-size:8.5px;line-height:12px}
.foot-link{left:123px;top:1136px;color:#ddd;font-size:8.5px;text-decoration:underline}
.follow{left:310px;top:1091px;width:188px;text-align:center;color:#fff;font-size:12.5px;font-weight:700;letter-spacing:.5px}
.social{top:1121px;width:27px;height:27px;border-radius:50%;background:#2d5aa8;border:2px solid #ddd}
.partner{background:#5a5a5a;border-radius:4px}
.copy{left:0;top:1173px;width:847px;height:27px;background:var(--footer-bar);color:#ccc;font-size:8.5px;text-align:center;line-height:27px}
</style>
</head>
<body>

<header>
  <div class="abs brand-mark"><div class="dot"></div><span>FERNDALE CREST</span></div>
  <div class="abs site-title">Ferndale Crest College</div>
  <div class="abs tagline">Stepping Ahead in Education, Culture, Sport &amp; Life</div>
  <div class="abs contact phone">
    <svg width="13" height="13" viewBox="0 0 24 24"><path fill="#1d3b22" d="M6.6 10.8a15 15 0 0 0 6.6 6.6l2.2-2.2c.3-.3.7-.4 1-.2 1.1.4 2.3.6 3.6.6.6 0 1 .4 1 1V20c0 .6-.4 1-1 1A17 17 0 0 1 3 4c0-.6.4-1 1-1h3.5c.6 0 1 .4 1 1 0 1.3.2 2.5.6 3.6.1.3 0 .7-.2 1z"/></svg>
    0774301582 / 0774309916
  </div>
  <div class="abs contact mail">
    <svg width="14" height="10" viewBox="0 0 14 10"><rect width="14" height="10" fill="#333"/><path d="M0 0l7 6 7-6" stroke="#fff" stroke-width="1.2" fill="none"/></svg>
    office@ferndalecrest.com
  </div>
  <form class="abs search"><input value="Search...."><button type="button">GO</button></form>
</header>

<nav class="abs nav">
  <a class="current" href="#" style="left:80px;width:94px"><span>HOME</span></a>
  <a href="#" style="left:174px;width:82px">ABOUT US</a>
  <a href="#" style="left:256px;width:94px">ACADEMICS</a>
  <a href="#" style="left:350px;width:86px">SPORTS</a>
  <a href="#" style="left:436px;width:137px">JOINING FERNDALE</a>
  <a href="#" style="left:573px;width:88px">ABOUT US</a>
  <a href="#" style="left:661px;width:110px">CONTACT US</a>
</nav>

<div class="abs hero" role="img" aria-label="Photo of a teacher helping young pupils writing with pencils in a classroom"></div>
<div class="abs hero-caption">
  <div class="main">Quality Education</div>
  <div class="sub">A Community Commitment</div>
</div>

<main class="abs main-col">
  <h1>Welcome to Ferndale Crest College</h1>
  <p>Welcome to <strong class="accent">Ferndale Crest Group of Schools</strong> where our School Motto is ‘Kelvora’ meaning Togetherness. We aim to work together in every aspect of School life, from academics to sport.</p>
  <p>Ferndale Crest College opened on 14th February 1983 and occupies 120 ha of land amidst the low hills of the Maple Ridge Range, 8km west of Ashbury. This location encourages focus on School life away from the distractions and hustle and bustle of the larger towns.</p>
  <p>The day scholars have the option of selected bus drop off points for parents to collect day scholars closer to home.</p>
  <p>Ferndale Crest College offers a wide range of academic subjects alongside a varied sport and extra-curricular program.</p>

  <h2 style="margin-top:18px">Headmaster's Message</h2>
  <div class="head-msg">
    <div class="head-photo" role="img" aria-label="Portrait photo of the headmaster"></div>
    <div>
      <p><strong>Welcome to Ferndale Crest College. Here at the College we aim to encourage each pupil to be a self-confident, well-rounded individual.</strong></p>
      <p>We aim to propel them to the highest level of achievement in both academics and extra-curricular activities to provide them with the life skills they will need when they leave the College and to prepare them to be of value to society.</p>
    </div>
  </div>
  <p>The College is a warm community which lives out high standards and is rightly proud of its achievements. We are a small enough School for each pupil to be known well, but large enough to offer a wide range of subjects and experience.</p>
  <p>Our Website covers many aspects of the College from how to apply for a place, to the curriculum and to much more. I hope you find it helpful and interesting.</p>
  <p style="margin-top:28px">Please visit and meet the pupils, the staff and see for yourself what Ferndale Crest College can offer your son or daughter. I look forward to welcoming you and your family to Ferndale Crest College.</p>
</main>

<aside>
  <form class="abs signup">
    <h3>Email Sign Up</h3>
    <p>If you would like to be added to the list of parents that receive the School Newsletter,</p>
    <input value="Enter Your name">
    <input value="Enter Your email">
    <button type="button">SUBSCRIBE</button>
  </form>

  <section class="abs side-block" style="top:685px">
    <h2>Upcoming Events</h2>
    <div class="side-rule"></div>
    <ul class="side-list events">
      <li>Robotic competitions teach students</li>
      <li>Robotic competitions teach students how to</li>
      <li>Robotic competitions teach</li>
      <li>Robotic competitions teach students</li>
      <li>Robotic competitions teach</li>
    </ul>
  </section>

  <section class="abs side-block" style="top:871px">
    <h2>Important Links</h2>
    <div class="side-rule"></div>
    <ul class="side-list links">
      <li>School Calender</li>
      <li>Registration Form</li>
      <li>Sports Announcements</li>
      <li>2nd Term 2014 Termly Calendar</li>
    </ul>
  </section>
</aside>

<footer>
  <div class="abs footer"></div>
  <svg class="abs foot-pin" width="33" height="44" viewBox="0 0 33 44"><path d="M16.5 0A16.5 16.5 0 0 0 0 16.5C0 29 16.5 44 16.5 44S33 29 33 16.5A16.5 16.5 0 0 0 16.5 0z" fill="#777"/><circle cx="16.5" cy="16" r="6" fill="#262626"/></svg>
  <div class="abs foot-name">Ferndale Crest College</div>
  <div class="abs foot-addr">12 Alder Lane,<br>Brookvale Vic 3042</div>
  <a class="abs foot-link" href="#">Click here to see the directions &gt;&gt;</a>
  <div class="abs foot-sep" style="left:310px"></div>
  <div class="abs follow">Follow Us On:</div>
  <div class="abs social" style="left:373px" aria-label="Social page"></div>
  <div class="abs social" style="left:409px;background:#3b8fd6" aria-label="Social feed"></div>
  <div class="abs foot-sep" style="left:498px"></div>
  <div class="abs partner" style="left:535px;top:1084px;width:72px;height:28px"></div>
  <div class="abs partner" style="left:624px;top:1082px;width:76px;height:30px"></div>
  <div class="abs partner" style="left:527px;top:1124px;width:88px;height:30px"></div>
  <div class="abs partner" style="left:624px;top:1126px;width:78px;height:28px"></div>
  <div class="abs partner" style="left:720px;top:1084px;width:50px;height:62px;border-radius:6px 6px 25px 25px;background:#8a8a8a"></div>
  <div class="abs copy">Copyright © 2015 Ferndale Crest. All Rights Reserved.</div>
</footer>

</body>
</html>
```